Speaker Overview Package

WHAT I NEED:
A professional speaker package INSPIRED BY Corinne Lasalle Brody example found in the attached url or by following this link: https://files.quorvanta.net/d/7KpLx2RwQm9ZtVbN4sYhJ3dFgC8aE1uT/open?mode=view
Same page types and structure, but with YOUR original creative design using Brelvo Reach branding: www.BrelvoReach.net
USE ATTACHED PDF FOR:
Page structure and content sections (what pages to include)
Professional quality level to match
Type of information on each page
Overall organization and flow
YOUR ORIGINAL DESIGN SHOULD INCLUDE:
Same page types (bio, topics, pricing, testimonials, etc.)
Brelvo Reach (www.BrelvoReach.net) branding from brelvoreach.net (colors, fonts, style)
Your own creative layout and design approach
Professional, corporate-friendly aesthetic
REQUIRED PAGE TYPES (like the example):
Cover page
Speaker bio/credentials
Methodology/approach page
Speaking topics (3-4 keynotes)
Testimonials
Event types offered
Pricing/packages
Workshop pricing
Client logos
Press/media mentions
Contact/booking
DELIVERABLES:
Original creative design (not copied from example)
Brelvo branding from brelvoreach.net
Print-ready PDF (300 DPI) + source files
8.5" x 11" format
Professional quality matching reference
SUBMIT FOR ENTRY:
Cover page concept
2-3 sample interior pages showing your design style
CRITICAL:
Use the example for STRUCTURE and CONTENT TYPES only. I want YOUR creative design using Brelvo branding. NO copying Corinne's graphics/layout. NO AI-generated designs.

```html
<!DOCTYPE html>
<html lang="en">
<head>
<meta charset="utf-8">
<title>Brelvo Reach — Speaker Overview Package</title>
<link href="https://fonts.googleapis.com/css2?family=Bebas+Neue&family=Playfair+Display:wght@700;900&family=Montserrat:wght@400;500;600;700&family=Poppins:wght@400;600&display=swap" rel="stylesheet">
<style>
:root{
  --red:#d40d12;
  --red-deep:#a8050a;
  --maroon:#3a0003;
  --ink:#151515;
  --charcoal:#1f1f1f;
  --grey:#555;
  --mist:#ececec;
  --white:#fff;
  --paper:#fff;
}
*{margin:0;padding:0;box-sizing:border-box}
html,body{width:1200px;height:927px;overflow:hidden;background:var(--paper)}
body{position:relative;font-family:"Poppins",sans-serif;color:var(--ink)}
.page{position:absolute;overflow:hidden;background:var(--white);box-shadow:0 2px 8px rgba(0,0,0,.28)}

/* cover */
.cover{left:45px;top:113px;width:485px;height:685px;background:var(--maroon)}
.cover-photo{position:absolute;inset:0;background:
  radial-gradient(ellipse 120px 190px at 320px 290px,#8a1d25 0%,#5c1a2a 45%,transparent 80%),
  radial-gradient(ellipse 260px 240px at 110px 280px,#2f6f86 0%,#1f4257 45%,transparent 80%),
  linear-gradient(180deg,#4a0508 0%,#3b1222 40%,#6d0a10 100%)}
.cover-shapes{position:absolute;inset:0}
.brand{position:absolute;left:49px;top:58px;display:flex;align-items:center;gap:8px;font-family:"Montserrat",sans-serif;font-weight:700;font-size:46px;line-height:1;color:var(--white);letter-spacing:-1px}
.brand-mark{width:34px;height:34px;background:var(--red)}
.cover-lead{position:absolute;left:49px;top:318px;font-family:"Montserrat",sans-serif;font-weight:500;font-size:22.5px;line-height:1;color:var(--white);letter-spacing:.4px}
.cover-big{position:absolute;left:47px;font-family:"Playfair Display",serif;font-weight:700;color:var(--white);line-height:1;font-size:54px;letter-spacing:-1.5px}
.cover-big.one{top:340px}
.cover-big.two{top:392px}
.cover-tail{position:absolute;left:49px;top:442px;font-family:"Montserrat",sans-serif;font-weight:600;font-size:23px;line-height:1;color:var(--white);letter-spacing:.5px}
.speaker{position:absolute;left:49px;top:514px;color:var(--white);font-family:"Montserrat",sans-serif;width:250px}
.speaker-label{font-weight:600;font-size:9.8px}
.speaker-name{font-size:8.6px;margin-top:7px}
.speaker-role{font-size:8.6px;margin-top:13px}
.speaker-offer{font-size:9.4px;line-height:1.3;margin-top:15px;width:140px}
.cover-band{position:absolute;left:0;bottom:0;width:100%;height:26px;background:var(--maroon)}

/* shared interior type */
.eyebrow{position:absolute;font-size:4.6px;color:var(--red);letter-spacing:.2px}
.headline{position:absolute;font-family:"Bebas Neue",sans-serif;font-size:17px;line-height:.98;color:var(--ink)}
.subhead{font-family:"Playfair Display",serif;font-weight:700;color:var(--red);font-size:7.3px}
.copy{font-size:3.25px;line-height:1.85;color:var(--grey)}
.copy b{color:var(--ink);font-weight:600}
.bullets{list-style:none;font-size:3.3px;line-height:1.9;color:var(--grey)}
.bullets li{position:relative;padding-left:6px}
.bullets li::before{content:"";position:absolute;left:1px;top:1.5px;width:1.4px;height:1.4px;border-radius:50%;background:var(--ink)}
.top-band{position:absolute;left:0;top:0;width:100%;height:12px;background:var(--red)}
.photo{position:absolute}
.dot-field{position:absolute;background:rgba(212,13,18,.06)}

/* bio */
.bio{left:603px;top:117px;width:228px;height:323px}
.bio-swoosh{position:absolute;left:0;top:0;width:100%;height:100%}
.bio .about{position:absolute;left:23px;top:71px}
.bio .intro{position:absolute;left:23px;top:83px;width:125px;text-align:justify}
.bio .intro p+p{margin-top:5px}
.bio .portrait{left:151px;top:73px;width:54px;height:77px;background:linear-gradient(180deg,#5a5a5a 0%,#2b2b2b 60%,#e8e8e8 100%)}
.cred-box{position:absolute;left:23px;top:160px;width:182px;height:68px;background:var(--charcoal);padding:8px 9px}
.cred-box .subhead{font-weight:400;font-size:7.3px}
.cred-box .bullets{color:#d8d8d8;margin-top:3px;font-size:2.9px;line-height:1.95}
.cred-box .bullets li::before{background:#d8d8d8}
.bio .style{position:absolute;left:23px;top:240px}
.bio .style-list{position:absolute;left:23px;top:251px;width:150px}

/* method */
.method{left:897px;top:117px;width:228px;height:323px}
.method .headline{left:23px;top:34px;font-size:16.5px}
.method .m-title{position:absolute;left:23px;top:56px}
.method .m-body{position:absolute;left:23px;top:68px;width:185px}
.steps{list-style:none;margin-top:1px;padding-left:3px}
.method .approach{position:absolute;left:23px;top:121px}
.method .approach-list{position:absolute;left:23px;top:132px;width:93px}
.method .gain{position:absolute;left:23px;top:196px}
.method .gain-list{position:absolute;left:23px;top:208px;width:93px}
.method .tower{left:120px;top:136px;width:86px;height:164px;border-radius:2px;background:linear-gradient(160deg,#b9b9b9 0%,#6f6f6f 35%,#1c1c1c 75%,#0c0c0c 100%)}

/* topics */
.topics{left:603px;top:475px;width:228px;height:322px}
.topics .strip{left:0;top:12px;width:58px;height:310px;background:linear-gradient(160deg,#5c5c5c 0%,#1a1a1a 40%,#3a3a3a 60%,#0a0a0a 100%)}
.topics .headline{left:63px;top:24px;font-size:17px}
.topics .dot-field{left:160px;top:16px;width:45px;height:45px}
.keynotes{position:absolute;left:63px;top:65px;width:145px}
.keynote{margin-bottom:4.2px}
.k-title{font-family:"Playfair Display",serif;color:var(--red);font-size:4.7px;border-left:1.6px solid var(--ink);padding-left:5px;line-height:1.1}
.k-sub{font-size:2.6px;font-weight:600;color:var(--ink);padding-left:6.6px;margin-top:1.3px}
.k-body{font-size:2.55px;line-height:1.75;color:var(--grey);margin-top:3.2px}
.k-label{font-size:2.6px;font-weight:600;color:var(--ink);margin-top:2.4px}
.ticks{list-style:none;font-size:2.55px;line-height:1.75;color:var(--grey);margin-top:1.5px}
.ticks li::before{content:"✓ ";color:var(--red)}

/* testimonials */
.reviews{left:897px;top:480px;width:228px;height:323px}
.reviews .headline{left:23px;top:70px;font-size:17px}
.reviews .dot-field{left:163px;top:22px;width:42px;height:43px}
.side-note{position:absolute;left:-44px;top:167px;width:142px;height:25px;transform:rotate(-90deg);font-size:3px;line-height:1.65;color:var(--grey)}
.avatar{position:absolute;left:75px;width:44px;height:44px;border-radius:50%;background:radial-gradient(circle at 50% 40%,#8b6a5a 0%,#3b2a24 60%,#1a1a1a 100%)}
.quote{position:absolute;left:131px;width:74px;border-left:1.6px solid var(--ink);padding-left:4px}
.quote p{font-size:2.75px;line-height:1.6;font-weight:600;color:var(--ink)}
.quote .who{font-size:2.5px;font-weight:400;color:var(--grey);margin-top:2px;line-height:1.3}
</style>
</head>
<body>

<!-- Cover -->
<section class="page cover">
  <div class="cover-photo" role="img" aria-label="Studio microphone photographed against a blue and red acoustic backdrop"></div>
  <svg class="cover-shapes" viewBox="0 0 485 685" width="485" height="685" aria-hidden="true">
    <defs>
      <linearGradient id="sweep" x1="0" y1="1" x2="1" y2="0">
        <stop offset="0" stop-color="#c4030a"/>
        <stop offset=".6" stop-color="#b3050b"/>
        <stop offset="1" stop-color="#d8141a"/>
      </linearGradient>
    </defs>
    <path d="M0 500 C 170 470 390 330 485 115 L485 685 L0 685 Z" fill="url(#sweep)"/>
    <path d="M0 560 C 200 520 410 420 485 300 L485 685 L0 685 Z" fill="#c0060c" opacity=".55"/>
  </svg>
  <div class="dot-field" style="left:415px;top:97px;width:55px;height:118px;background:rgba(255,255,255,.06)" role="img" aria-label="Dot grid pattern"></div>
  <div class="brand"><span>BRELVO</span><span class="brand-mark"></span></div>
  <div class="cover-lead">UNLOCK PERFORMANCE</div>
  <div class="cover-big one">ACCELERATE</div>
  <div class="cover-big two">IMPACT</div>
  <div class="cover-tail">TRANSFORM CULTURE</div>
  <div class="speaker">
    <div class="speaker-label">Speaker Name:</div>
    <div class="speaker-name">Grant L. Whitfield</div>
    <div class="speaker-role">Founder &amp; CEO, Brelvo Reach</div>
    <div class="speaker-offer">Keynotes • Workshops • Leadership Development • Organizational Performance</div>
  </div>
  <div class="cover-band"></div>
</section>

<!-- Speaker bio -->
<section class="page bio">
  <svg class="bio-swoosh" viewBox="0 0 228 323" width="228" height="323" aria-hidden="true">
    <circle cx="180" cy="170" r="170" fill="var(--mist)" opacity=".8"/>
    <circle cx="180" cy="170" r="110" fill="#fff"/>
  </svg>
  <div class="eyebrow" style="left:23px;top:23px">INTRODUCTION</div>
  <h2 class="headline" style="left:23px;top:33px">SPEAKER BIO /<br>CREDENTIALS</h2>
  <h3 class="subhead about">About Elias Navarro Voss</h3>
  <div class="copy intro">
    <p>Elias graduated from Redmont State with a teaching degree in 1999. While teaching, he was hired to travel the state of Texas teaching teachers his passion for motivating his students and strategies to help his students learn. It was during this time that Elias refined his skills for speaking, which would later become his sweet spot.</p>
    <p>Elias continued his education with a Masters degree in education administration from Redmont Tech University in 2005. After teaching for 11 years, Elias decided to be a full-time consultant with the same company he had helped for many years, Halvern-Pike.</p>
  </div>
  <div class="photo portrait" role="img" aria-label="Portrait of the speaker in a white shirt and dark tie"></div>
  <div class="cred-box">
    <h3 class="subhead">Credentials &amp; Expertise</h3>
    <ul class="bullets">
      <li>Leadership &amp; Team Performance Strategist</li>
      <li>Certified Executive &amp; Organizational Coach</li>
      <li>Former Organizational Development Director</li>
      <li>15+ years of experience developing leaders and high-performance teams</li>
      <li>Trusted consultant for corporations, nonprofits, government, and community organizations</li>
    </ul>
  </div>
  <h3 class="subhead style">Elias's Speaking Style</h3>
  <ul class="bullets style-list">
    <li><b>Engaging</b> storytelling</li>
    <li><b>Research-backed</b> insights</li>
    <li><b>Practical</b> tools and behaviors leaders can apply immediately</li>
    <li><b>Interactive,</b> energizing delivery</li>
  </ul>
</section>

<!-- Method & approach -->
<section class="page method">
  <div class="top-band"></div>
  <h2 class="headline">BRELVO IMPACT METHOD &amp; APPROACH</h2>
  <h3 class="subhead m-title">The Brelvo Impact Method™</h3>
  <div class="copy m-body">
    <p>Rooted in behavioral science, leadership psychology, and high-performance research, the Brelvo Impact Method™ equips leaders with practical tools to:</p>
    <ol class="steps">
      <li>1. <b>Lead Themselves</b> – Self-awareness, emotional intelligence, clarity</li>
      <li>2. <b>Lead Others</b> – Communication, coaching, and collaboration</li>
      <li>3. <b>Lead the Organization</b> – Culture building, strategy, and alignment</li>
      <li>4. <b>Lead for Impact</b> – Sustained transformation that drives measurable results</li>
    </ol>
  </div>
  <h3 class="subhead approach">Our Approach</h3>
  <ul class="bullets approach-list">
    <li><b>Evidence-based:</b> Built on modern research in leadership, performance, and motivation</li>
    <li><b>Human-centered:</b> Designed around real people, real challenges, real behaviors</li>
    <li><b>Action-driven:</b> Every keynote and workshop provides tools that can be used today</li>
    <li><b>Culturally adaptable:</b> Tailored for diverse teams, industries, and organizational goals</li>
  </ul>
  <h3 class="subhead gain">What Audiences Gain</h3>
  <ul class="bullets gain-list">
    <li>New ways to communicate with clarity and influence</li>
    <li>Tools to reduce friction and build psychological safety</li>
    <li>Frameworks to improve decision-making and resilience</li>
    <li>Practical steps to elevate team performance and culture</li>
  </ul>
  <div class="photo tower" role="img" aria-label="Black and white photo of a modern office tower"></div>
</section>

<!-- Speaking topics -->
<section class="page topics">
  <div class="top-band"></div>
  <div class="photo strip" role="img" aria-label="Dark architectural photo of angled building slats"></div>
  <h2 class="headline">SPEAKING<br>TOPICS</h2>
  <div class="dot-field" role="img" aria-label="Red dot grid pattern"></div>
  <div class="keynotes">
    <article class="keynote">
      <h4 class="k-title">KEYNOTE 1: Leadership by Design™</h4>
      <div class="k-sub">How Intentional Leaders Communicate, Inspire, and Drive Results</div>
      <p class="k-body">Great leadership doesn't happen by accident — it's designed through daily behaviors, communication patterns, and intentional influence. This keynote teaches leaders how to architect trust, clarity, and accountability inside their teams.</p>
      <div class="k-label">Key Outcomes:</div>
      <ul class="ticks"><li>How to communicate with clarity and confidence</li><li>Tools for building trust through consistent leadership cues</li><li>How to connect purpose to performance</li><li>A step-by-step model for designing a leadership identity</li></ul>
    </article>
    <article class="keynote">
      <h4 class="k-title">KEYNOTE 2: The High-Performance Leader™</h4>
      <div class="k-sub">Unlocking the Mindsets, Habits &amp; Systems of Top Performers</div>
      <p class="k-body">Top performing leaders think differently, act intentionally, and build systems that enable momentum. This keynote reveals the high-performance principles that elevate productivity without burnout.</p>
      <div class="k-label">Key Outcomes:</div>
      <ul class="ticks"><li>The 4 high-performance accelerators</li><li>How to remove friction and increase alignment</li><li>Strategies for improving focus, accountability, and execution</li><li>Tools for leading high-performance conversations</li></ul>
    </article>
    <article class="keynote">
      <h4 class="k-title">KEYNOTE 3: The Culture Advantage™</h4>
      <div class="k-sub">How to Build Teams That Are Connected, Confident &amp; Collaborative</div>
      <p class="k-body">Culture is not what leaders say — it's what teams experience every day. This keynote breaks down the psychology of healthy team dynamics and equips leaders to build cultures that win.</p>
      <div class="k-label">Key Outcomes:</div>
      <ul class="ticks"><li>How to strengthen communication and reduce misalignment</li><li>Why psychological safety drives performance</li><li>Tools for resolving conflict and improving team relationships</li><li>Strategies for creating a culture of shared ownership</li></ul>
    </article>
    <article class="keynote">
      <h4 class="k-title">KEYNOTE 4: Communication that Moves People™</h4>
      <div class="k-sub">The Art and Science of Influence, Presence &amp; Connection</div>
      <p class="k-body">Communication is the leader's greatest leverage point. In this engaging keynote, Grant reveals the verbal and non-verbal cues that shape trust, credibility, and leadership presence.</p>
      <div class="k-label">Key Outcomes:</div>
      <ul class="ticks"><li>How leaders signal trust, competence, and connection</li><li>Communication frameworks for difficult conversations</li><li>Strategies to build influence across any environment</li><li>How to increase confidence and resonance on every platform</li></ul>
    </article>
  </div>
</section>

<!-- Testimonials -->
<section class="page reviews">
  <div class="top-band"></div>
  <div class="dot-field" role="img" aria-label="Red dot grid pattern"></div>
  <h2 class="headline">TESTIMONIALS</h2>
  <p class="side-note">Our clients consistently share how Brelvo Reach has transformed the way their leaders communicate, collaborate, and perform. These testimonials highlight the real-world results, personal breakthroughs, and organizational shifts achieved through our keynotes and leadership programs.</p>
  <div class="avatar" style="top:100px" role="img" aria-label="Portrait of a client"></div>
  <div class="avatar" style="top:153px" role="img" aria-label="Portrait of a client"></div>
  <div class="avatar" style="top:219px" role="img" aria-label="Portrait of a client"></div>
  <blockquote class="quote" style="top:108px">
    <p>"Elias has helped challenge me and bring out what I knew I had in me. I feel we are just getting started and I always look forward to our next meetings. I highly recommend Elias Navarro!"</p>
    <div class="who">Marisol Fuentes<br>Keystone Realty Agent</div>
  </blockquote>
  <blockquote class="quote" style="top:160px">
    <p>"Where do I start to write a review about Elias!!! The guy is an incredible speaker! Our Real Estate Team recently had our yearly team meeting to prepare for next year and we had Elias speak. It was a very impactful session and really hit home with our Team. I would highly recommend Elias if you are considering having speaker at an event, you WILL NOT be disappointed."</p>
    <div class="who">Colby Harlan<br>Harlan &amp; Co. Team</div>
  </blockquote>
  <blockquote class="quote" style="top:227px">
    <p>"I would give Elias Navarro the highest recommendation for any business, coaching or mentoring opportunity."</p>
    <div class="who">Renata Solis<br>Business Development / Marketing</div>
  </blockquote>
</section>

</body>
</html>
```